Card design for orthopaedic surgeons working as The Brightwater Joint Centre

Business cards, letterhead

Colors

Designer to choose colors to be used in the design.

Requirements
Must have
• Late addition.
• Cards letterhead must have logos of
• Crestmoor Lindell College of Surgeons
• Varenwood Bone Health Association
Nice to have
• Back of card to have space for appointment time to be added by hand and some blank space for writing incidental other notes.

```html
<!DOCTYPE html>
<html lang="en">
<head>
<meta charset="utf-8">
<title>The Brightwater Joint Centre — Business Card</title>
<link rel="stylesheet" href="https://fonts.googleapis.com/css2?family=Questrial&display=swap">
<style>
  :root {
    --stage: #2b2b2d;
    --navy: #032a47;
    --sky: #35b4f4;
    --sky-deep: #1f9fe6;
    --badge: #0d4a74;
    --white: #ffffff;
  }
  * { box-sizing: border-box; margin: 0; padding: 0; }
  html, body {
    width: 1200px; height: 750px; overflow: hidden;
    background: var(--stage);
    font-family: "Questrial", "Helvetica Neue", Arial, sans-serif;
  }
  .canvas {
    position: relative; width: 1200px; height: 750px;
    display: flex; align-items: center; justify-content: center; gap: 40px;
  }
  .card {
    position: relative; width: 520px; height: 297px;
    border-radius: 16px; overflow: hidden;
    box-shadow: 0 10px 28px rgba(0,0,0,.45);
  }
  .card-back { background: var(--navy); }
  .card-back .brand-name {
    position: absolute; left: 0; right: 0; top: 50%;
    transform: translateY(-50%);
    text-align: center; color: var(--sky);
    font-size: 26px; letter-spacing: .2px;
  }
  .affiliations {
    position: absolute; left: 0; right: 0; bottom: 22px;
    display: flex; justify-content: center; gap: 14px; list-style: none;
  }
  .affiliation-badge {
    width: 26px; height: 26px; border-radius: 50%;
    background: var(--badge);
  }
  .card-front { background: var(--sky); }
  .card-front .wave { position: absolute; inset: 0; }
  .person {
    position: absolute; left: 40px; top: 128px; color: var(--white);
  }
  .person-name { font-size: 24px; line-height: 1.1; }
  .person-role { font-size: 14px; margin-top: 2px; }
  .contact {
    position: absolute; right: 22px; top: 14px;
    color: var(--white); font-size: 11.5px; line-height: 1.4;
    text-align: right; list-style: none;
  }
  .contact li { display: flex; justify-content: flex-end; align-items: center; gap: 6px; }
  .contact .address { padding-right: 18px; }
  .contact svg { width: 12px; height: 12px; flex: none; }
  .card-front .brand-name {
    position: absolute; right: 24px; bottom: 26px;
    color: var(--sky-deep); font-size: 24px; white-space: nowrap;
  }
</style>
</head>
<body>
<main class="canvas">

  <section class="card card-back" aria-label="Card back">
    <p class="brand-name">The Brightwater Joint Centre</p>
    <ul class="affiliations">
      <li class="affiliation-badge" role="img" aria-label="Crestmoor Lindell College of Surgeons badge"></li>
      <li class="affiliation-badge" role="img" aria-label="Varenwood Bone Health Association badge"></li>
    </ul>
  </section>

  <section class="card card-front" aria-label="Card front">
    <svg class="wave" viewBox="0 0 520 297" aria-hidden="true">
      <path d="M520,76 C480,170 395,175 292,180 C180,186 108,216 76,297" fill="none" stroke="#fff" stroke-width="2"/>
      <path d="M520,88 C482,180 400,184 300,190 C190,198 120,227 90,297 L520,297 Z" fill="#fff"/>
      <path d="M118,290 C140,244 180,214 250,204" fill="none" stroke="var(--navy)" stroke-width="3" stroke-linecap="round"/>
    </svg>

    <div class="person">
      <p class="person-name">Owen Hartley</p>
      <p class="person-role">President</p>
    </div>

    <ul class="contact">
      <li class="address">4127 Larkfield Avenue</li>
      <li class="address">Ashby Vale, NY 10990</li>
      <li>(555) 0142-7781
        <svg viewBox="0 0 12 12"><path d="M2 4 Q6 1 10 4 L9 5.5 L7.5 4.8 L7.5 4 Q6 3.4 4.5 4 L4.5 4.8 L3 5.5 Z M3.5 6 H8.5 L9.5 10 H2.5 Z" fill="#fff"/></svg></li>
      <li>(555) 0193-4406
        <svg viewBox="0 0 12 12"><rect x="3.5" y="1" width="5" height="10" rx="1" fill="none" stroke="#fff" stroke-width="1.2"/></svg></li>
      <li>info@brightwaterjoint.com
        <svg viewBox="0 0 12 12"><rect x="1" y="3" width="10" height="6.5" fill="#fff"/><path d="M1 3 L6 7 L11 3" fill="none" stroke="var(--sky)" stroke-width="1"/></svg></li>
      <li>brightwaterjoint.com
        <svg viewBox="0 0 12 12"><circle cx="6" cy="6" r="5" fill="#fff"/><ellipse cx="6" cy="6" rx="2" ry="5" fill="none" stroke="var(--sky)" stroke-width=".8"/><path d="M1 6 H11" stroke="var(--sky)" stroke-width=".8"/></svg></li>
    </ul>

    <p class="brand-name">The Brightwater Joint Centre</p>
  </section>

</main>
</body>
</html>
```